FunBrixo Business Card

We need a business card design for our company. We sell construction-themed amusement rides for kids.

Contact Information for Business Card

Contact info on business card should include:
Carl Dunning
Co-Founder & COO
(833) 571-FUNBRIX
Carl@funbrixo-demo.com
www.funbrixo-demo.com

```html
<!DOCTYPE html>
<html lang="en">
<head>
<meta charset="utf-8">
<title>FunBrixo Business Card</title>
<link rel="stylesheet" href="https://fonts.googleapis.com/css2?family=Oswald:wght@300;400;700&display=swap">
<style>
  :root {
    --backdrop: #d6d6d8;
    --card: #fbfbfa;
    --orange: #e07a2c;
    --blue: #2fa9e4;
    --purple: #7b2f9a;
    --pink: #e0338f;
    --gold: #f2b526;
    --ink: #5a5a5a;
    --rule: #d9a27a;
  }
  * { margin: 0; padding: 0; box-sizing: border-box; }
  html, body { width: 1200px; height: 848px; overflow: hidden; }
  body {
    background: var(--backdrop);
    font-family: "Oswald", sans-serif;
    display: flex;
    flex-direction: column;
    align-items: center;
    justify-content: center;
    gap: 48px;
  }
  .card {
    width: 525px;
    height: 300px;
    background: var(--card);
    box-shadow: 0 6px 18px rgba(0,0,0,0.12);
    position: relative;
    display: flex;
    align-items: center;
  }
  .brand {
    display: flex;
    align-items: center;
    gap: 12px;
    font-family: "Oswald", sans-serif;
    font-weight: 700;
    color: var(--orange);
    line-height: 1;
  }
  .brand-dot {
    width: 22px; height: 22px;
    border-radius: 50%;
    background: var(--purple);
    flex: none;
  }
  /* front */
  .card-front { padding: 0 40px 0 36px; justify-content: space-between; }
  .card-front .brand { font-size: 48px; }
  .contact { width: 200px; text-align: center; }
  .contact-name {
    font-family: "Oswald", sans-serif;
    font-weight: 700;
    font-size: 30px;
    letter-spacing: 1px;
    text-transform: uppercase;
    line-height: 1.1;
  }
  .c1 { color: var(--orange); } .c2 { color: var(--blue); }
  .c3 { color: var(--purple); } .c4 { color: var(--pink); }
  .c5 { color: var(--gold); }
  .contact-title {
    font-weight: 400;
    font-size: 12px;
    letter-spacing: 1.5px;
    color: var(--orange);
    text-transform: uppercase;
    margin-top: 4px;
  }
  .contact-rule {
    width: 44px; height: 2px;
    background: var(--rule);
    margin: 16px auto 16px;
  }
  .contact-line {
    font-weight: 300;
    font-size: 12px;
    letter-spacing: 1px;
    color: var(--ink);
    text-transform: uppercase;
    line-height: 1.6;
  }
  /* back */
  .card-back { justify-content: center; }
  .card-back .brand { font-size: 56px; }
</style>
</head>
<body>
  <section class="card card-front" aria-label="Business card front">
    <div class="brand"><span class="brand-dot"></span>FunBrixo</div>
    <div class="contact">
      <p class="contact-name">
        <span class="c1">C</span><span class="c2">a</span><span class="c3">r</span><span class="c4">l</span>
        <span class="c1">D</span><span class="c2">u</span><span class="c5">n</span><span class="c3">n</span><span class="c4">i</span><span class="c1">n</span><span class="c2">g</span>
      </p>
      <p class="contact-title">Co-Founder &amp; COO</p>
      <div class="contact-rule"></div>
      <p class="contact-line">(833) 571-FUNBRIX</p>
      <p class="contact-line">Carl@funbrixo-demo.com</p>
      <p class="contact-line">www.funbrixo-demo.com</p>
    </div>
  </section>

  <section class="card card-back" aria-label="Business card back">
    <div class="brand"><span class="brand-dot"></span>FunBrixo</div>
  </section>
</body>
</html>
```